Cutting Edge Property Services Provider is Looking to Update Business Card Design

We are looking to freshen up our business cards to match our cutting edge technology based image.

KORVANEX - Where Care Finds Its Pulse

More information about our company can be found on our website at www.korvanex-demo.net

We integrate technology in a historically low tech industry.

We have appeared on the Brisk 300/3000 list 2 years in a row and we're previously recognized as the 5th Quickest Rising Firm in San Diego.

Our core colors are blue and white, but are not against accents that might improve our image.

We currently have our Mission Statement on our Business Cards in a folding design:
KORVANEX IS THE LEADING BUILDING SERVICES INNOVATOR. BY COMBINING TECHNOLOGY WITH FUNCTIONAL TOOS THAT IMPROVE EFFICIENCY IN THE WORKPLACE, WE PROVIDE UNPARALLELED SERVICE IN THE INDUSTRY. DEVELOPING LASTING RELATIONSHIPS WITH OUR CLIENTS AND ASSOCIATES IS THE CORNERSTONE OF OUR SUCCESS.

We'd like to convey the image of a cutting edge, technology based company. Want the cards to pop.

Target Market(s)

Commercial Property Managers - 20 to 50 year old professionals

Industry/Entity Type

Business

Requirements
Must have
• Must utilize our logo obviously, but are definitely open to using variations on the logo. Utilizing the components of the logo, but maybe in different configurations or backgrounds, etc...

Must use the Name: KORVANEX.
Can also use KORVANEX PROPERTY SERVICES.

Must include the Mission Statement

Must say: Where Care Finds Its Pulse
Nice to have
• We are considering plastic stock, shaped cards, or folding cards.

Nothing over the top or really expensive, but will consider if it conveys innovation and technology.
Should not have
• No images of toilets, buildings, trees, or anything relating to commercial properties.

We want to convey our technology image.

```html
<!DOCTYPE html>
<html lang="en">
<head>
<meta charset="utf-8">
<title>KORVANEX – Folding Business Card</title>
<link rel="stylesheet" href="https://fonts.googleapis.com/css2?family=Source+Sans+3:wght@400;600;700;800&display=swap">
<style>
  :root {
    --stage: #2b2420;
    --brand-blue: #0f4f86;
    --brand-blue-deep: #0b3f6b;
    --brand-blue-soft: #1a5c94;
    --card-white: #ffffff;
    --ink: #1f2a33;
    --rule: #9aa6b2;
  }
  * { box-sizing: border-box; margin: 0; padding: 0; }
  html, body {
    width: 1200px; height: 802px; overflow: hidden;
    background: var(--stage);
    font-family: "Source Sans 3", Arial, sans-serif;
  }
  .sheet { position: relative; width: 1200px; height: 802px; }
  .card { position: absolute; overflow: hidden; }

  /* Inner top */
  .card--inner-top {
    left: 45px; top: 71px; width: 546px; height: 312px;
    background: var(--card-white); border-radius: 26px;
  }
  .wordmark {
    position: absolute; left: 0; right: 0;
    display: flex; align-items: center; justify-content: center; gap: 14px;
    font-weight: 800; color: var(--brand-blue); letter-spacing: 2px;
    white-space: nowrap;
  }
  .wordmark__square { background: var(--brand-blue); display: block; }
  .card--inner-top .wordmark { top: 108px; font-size: 56px; }
  .card--inner-top .wordmark__square { width: 40px; height: 40px; }
  .inner-top__url {
    position: absolute; left: 0; right: 0; top: 268px; text-align: center;
    font-size: 20px; letter-spacing: 4px; color: var(--ink);
  }

  /* Front */
  .card--front {
    left: 620px; top: 71px; width: 545px; height: 312px;
    background: var(--card-white);
    border-top: 10px solid var(--brand-blue-deep);
  }
  .card--front .wordmark { top: 68px; font-size: 46px; }
  .card--front .wordmark__square { width: 32px; height: 32px; }
  .front__identity {
    position: absolute; right: 267px; top: 198px; text-align: right;
    color: var(--ink); font-size: 13px; line-height: 1.45; white-space: nowrap;
  }
  .front__name { font-size: 19px; font-weight: 700; color: var(--brand-blue); line-height: 1.2; }
  .front__title { margin-bottom: 6px; }
  .front__divider {
    position: absolute; left: 292px; top: 198px; width: 1px; height: 82px;
    background: var(--rule);
  }
  .front__contacts {
    position: absolute; left: 302px; top: 198px; list-style: none;
    font-size: 13.5px; color: var(--ink); white-space: nowrap;
  }
  .front__contacts li { display: flex; align-items: center; gap: 7px; height: 29px; }
  .front__contacts svg { width: 11px; height: 11px; fill: var(--brand-blue); }

  /* Inner bottom */
  .card--inner-bottom {
    left: 45px; top: 402px; width: 546px; height: 312px;
    background: var(--brand-blue);
    display: flex; align-items: center; justify-content: center;
  }
  .mission {
    color: var(--card-white); text-align: center; text-transform: uppercase;
    font-size: 16.5px; line-height: 30px; white-space: nowrap;
  }

  /* Back */
  .card--back {
    left: 620px; top: 402px; width: 545px; height: 312px;
    background: radial-gradient(ellipse at center, var(--brand-blue-soft), var(--brand-blue) 70%);
  }
  .card--back .wordmark { top: 112px; font-size: 60px; color: var(--card-white); }
  .card--back .wordmark__square { width: 42px; height: 42px; background: var(--card-white); }
  .back__tagline {
    position: absolute; left: 0; right: 0; top: 252px; text-align: center;
    color: var(--card-white); font-weight: 700; font-size: 25px;
  }
</style>
</head>
<body>
<main class="sheet">

  <section class="card card--inner-top" aria-label="Inner top panel">
    <div class="wordmark"><span class="wordmark__square"></span>KORVANEX</div>
    <p class="inner-top__url">www.korvanex-demo.net</p>
  </section>

  <section class="card card--front" aria-label="Front panel">
    <div class="wordmark"><span class="wordmark__square"></span>KORVANEX</div>
    <div class="front__identity">
      <p class="front__name">Your Name</p>
      <p class="front__title">Title</p>
      <p>1480 Harbor Crest Blvd</p>
      <p>Suite 210, Lakemont, OR 97031</p>
    </div>
    <span class="front__divider"></span>
    <ul class="front__contacts">
      <li><svg viewBox="0 0 12 12"><path d="M2.5 1h2l1 3-1.3 1a6 6 0 0 0 2.8 2.8l1-1.3 3 1v2a1 1 0 0 1-1 1A10 10 0 0 1 1.5 2a1 1 0 0 1 1-1z"/></svg>1(800) 555-0142</li>
      <li><svg viewBox="0 0 12 12"><path d="M1 3h10v7H1z M1 3l5 4 5-4" fill="none" stroke="#0f4f86" stroke-width="1.4"/></svg>info@korvanex-demo.net</li>
      <li><svg viewBox="0 0 12 12"><circle cx="6" cy="6" r="5" fill="none" stroke="#0f4f86" stroke-width="1.2"/><path d="M1 6h10M6 1c-3 3-3 7 0 10M6 1c3 3 3 7 0 10" fill="none" stroke="#0f4f86" stroke-width="1"/></svg>www.korvanex-demo.net</li>
    </ul>
  </section>

  <section class="card card--inner-bottom" aria-label="Inner bottom panel">
    <p class="mission">KORVANEX is the leading building services innovator.<br>
      By combining technology with functional toos that<br>
      improve efficiency in the workplace, we provide<br>
      unparalleled service in the industry. Developing<br>
      lasting relationships with our clients and associates<br>
      is the cornerstone of our success.</p>
  </section>

  <section class="card card--back" role="img" aria-label="Back panel: blue background with a repeating brand pattern, wordmark and tagline">
    <div class="wordmark"><span class="wordmark__square"></span>KORVANEX</div>
    <p class="back__tagline">Where Care Finds Its Pulse</p>
  </section>

</main>
</body>
</html>
```